Cleaning Service Company In need of Good Web presence.

The company is a cleaning service company which provides professional staff and service for cleaning. This is a project to build a site that is both solid and a strong recognition of our organization. It is supposed to show quality, cleanliness, professionalism. The use of images and art for imagery is all good just to have a site that is consistent and solid. There might be a chance to make stationary, logo and business cars if someone feels they can build a brand that is consistent. The image we are going for is clean solid and to stand out. Finally stationary should not be expensive to print.

Current logo is attached and can be used or can be made more creative.

Target Market(s)

Corporate and Government entities, that will feel that this company has a brand that sets it apart from the rest. The company is new so the modification of the logo will not be an issue if a more solid brand come out of this project. The idea is to have a clean consistent product that stands our from others in terms of website, stationary, etc

Industry/Entity Type

Cleaning Service

Contact Information for Business Card

P.O.Box 51947
Riffa
Kingdom of Bahrain

Logo Text

Harbor Lane Services

Number of Pages Required

4 page

Font styles to use
Sans Serif

Colors
abd036
cadf82
eaf2ce
9bcb3b

Requirements
Must have
• Green Color to be used in order to stick to the name. Also the creativity and boldness in an elegant manner.
Nice to have
• Arabic name of company
• هاربر لين سرفسس ذ.م.م
• if cannot be put at least make a location should be chosen
• Also could be a bit of 3D given to the logo if it could stay elegent.
Should not have
• Should not show people cleaning.

```html
<!DOCTYPE html>
<html lang="en">
<head>
<meta charset="utf-8">
<title>Harbor Lane Services W.L.L</title>
<link rel="stylesheet" href="https://fonts.googleapis.com/css2?family=Montserrat:wght@400;600;700&family=Open+Sans:ital,wght@0,400;0,600;1,400;1,600&family=Cairo:wght@300;400&display=swap">
<style>
:root{
  --green:#abd036;
  --green-deep:#9bcb3b;
  --green-soft:#cadf82;
  --green-pale:#eaf2ce;
  --ink:#222222;
  --text:#6b6b6b;
  --muted:#9a9a9a;
  --line:#e2e2e2;
  --footer:#f5f5f5;
  --white:#ffffff;
}
*{box-sizing:border-box;margin:0;padding:0}
html,body{width:1200px;height:2446px;overflow:hidden}
body{position:relative;background:var(--white);font-family:"Open Sans",Arial,sans-serif;color:var(--text)}
.abs{position:absolute}
.heading{font-family:"Montserrat",Arial,sans-serif;color:var(--ink);font-weight:700}

/* header */
.topline{left:0;top:0;width:1200px;height:4px;background:var(--green)}
.header{left:0;top:4px;width:1200px;height:89px;background:var(--white)}
.nav a{position:absolute;top:40px;font-family:"Montserrat",sans-serif;font-size:12px;font-weight:600;color:var(--ink);text-decoration:none;letter-spacing:.3px}
.nav a.active{color:var(--green)}
.nav-leaf{left:440px;top:22px}
.search{left:1032px;top:27px;width:37px;height:37px;border-radius:50%;background:#ececec}
.brand{left:127px;top:14px;width:150px;height:150px;border-radius:50%;background:var(--white);z-index:5;display:flex;align-items:center;justify-content:center;text-align:center;box-shadow:0 2px 6px rgba(0,0,0,.08)}
.brand-name{font-family:"Montserrat",sans-serif;font-weight:700;font-size:17px;line-height:1.2;color:var(--green-deep);width:110px}

/* hero */
.hero{left:0;top:93px;width:1200px;height:513px;background:linear-gradient(180deg,#5f7da3 0%,#9fb4c9 35%,#7f8f8f 58%,#4f6b32 72%,#7aa33a 86%,#8eb545 100%)}
.hero-title{left:0;top:225px;width:1200px;text-align:center;font-family:"Cairo",sans-serif;font-weight:300;font-size:66px;color:var(--white);direction:rtl}
.hero-sub{left:300px;top:322px;width:600px;text-align:center;font-size:15px;line-height:28px;color:var(--white)}
.btn-solid{left:515px;top:400px;width:126px;height:34px;background:var(--green);border:1px solid var(--white);color:var(--white);font-family:"Montserrat",sans-serif;font-size:11px;font-weight:600;display:flex;align-items:center;justify-content:center}
.arrow{top:327px;width:44px;height:44px;border-radius:50%;background:rgba(60,60,60,.75);display:flex;align-items:center;justify-content:center}

/* welcome */
.welcome-title{left:132px;top:698px;font-size:22px}
.welcome-text{left:132px;width:590px;font-size:12px;line-height:25px}
.btn-outline{left:132px;top:878px;width:124px;height:35px;border:1px solid var(--green);color:var(--green);font-family:"Montserrat",sans-serif;font-size:11px;font-weight:600;display:flex;align-items:center;justify-content:center}
.welcome-photo{left:797px;top:665px;width:272px;height:272px;border-radius:50%;background:linear-gradient(180deg,#e8eef3 0%,#d9e1e4 55%,#8fb653 75%,#6f9a3a 100%);border-bottom:6px solid var(--green)}

/* services */
.services-photo{left:0;top:1000px;width:600px;height:480px;background:linear-gradient(135deg,#5b5755 0%,#3f3a38 50%,#2f2b2a 100%)}
.services-panel{left:600px;top:1000px;width:600px;height:480px;background:var(--green-pale)}
.services-badge{left:134px;top:1089px;width:339px;height:257px;background:rgba(171,208,54,.85);display:flex;align-items:center;justify-content:center;text-align:center;font-family:"Montserrat",sans-serif;font-weight:700;font-size:36px;line-height:46px;color:var(--white)}
.service-icon{left:562px;width:82px;height:82px;border-radius:50%;background:var(--green);border:4px solid var(--white);display:flex;align-items:center;justify-content:center}
.service-leaf{left:540px}
.service-title{left:660px;font-family:"Montserrat",sans-serif;font-weight:700;font-size:14px;color:var(--ink)}
.service-text{left:660px;width:410px;font-size:11.5px;line-height:22px}

/* blog */
.blog-title{left:0;top:1538px;width:1200px;text-align:center;font-size:24px}
.blog-sub{left:0;top:1572px;width:1200px;text-align:center;font-size:12px;color:#555}
.post-photo{top:1615px;width:289px;height:183px}
.post-title{top:1814px;font-family:"Montserrat",sans-serif;font-size:13px;font-weight:600;color:var(--ink)}
.post-text{top:1838px;width:289px;font-size:11.5px;line-height:23px}
.post-meta{top:1887px;font-size:11.5px;color:var(--green-deep);display:flex;align-items:center;gap:8px}
.post-meta .sep{color:#bbb;margin:0 8px}

/* testimonial */
.testimonial{left:0;top:1960px;width:1200px;height:146px;background:var(--green)}
.avatar{left:134px;top:1991px;width:84px;height:84px;border-radius:50%;border:3px solid var(--white);background:linear-gradient(180deg,#d8d2cc,#2c2a2a)}
.divider{left:252px;top:1984px;width:1px;height:98px;background:rgba(255,255,255,.5)}
.quote{left:285px;top:1994px;width:790px;font-style:italic;font-weight:600;font-size:13.5px;line-height:25px;color:var(--white)}
.quote-name{left:285px;top:2050px;font-size:11.5px;color:var(--white);letter-spacing:.5px}

/* footer */
.footer{left:0;top:2106px;width:1200px;height:340px;background:var(--footer)}
.footer-brand{left:134px;top:2176px;width:132px;height:132px;border-radius:50%;background:var(--white);display:flex;align-items:center;justify-content:center;text-align:center}
.footer-brand .brand-name{font-size:15px;width:100px}
.foot-head{top:2148px;font-family:"Montserrat",sans-serif;font-size:13px;font-weight:600;color:var(--ink)}
.foot-links{left:363px;top:2186px;list-style:none;font-size:11px;line-height:24px;color:#444}
.news-text{left:546px;top:2180px;width:260px;font-size:11px;line-height:22px;color:#555}
.news-input{left:546px;top:2248px;width:251px;height:41px;background:var(--white);border:1px solid var(--line);font-size:11px;color:#555;padding:13px 14px}
.news-btn{left:546px;top:2297px;width:85px;height:36px;border:1px solid var(--green);background:var(--white);color:var(--green);font-size:11px;display:flex;align-items:center;justify-content:center}
.contact-row{left:905px;display:flex;gap:12px;font-size:11px;line-height:17px;color:#555;width:170px}
.contact-row svg{flex:none;margin-top:2px}
.foot-rule{left:132px;top:2364px;width:936px;height:1px;background:var(--line)}
.copyright{left:132px;top:2392px;font-size:11px;color:#555}
.follow{left:830px;top:2392px;font-size:11px;color:#555}
.social{top:2384px;width:31px;height:31px;border-radius:50%;border:1.5px solid #555}
</style>
</head>
<body>

<div class="abs topline"></div>
<header class="abs header">
  <nav class="nav">
    <svg class="abs nav-leaf" width="20" height="12" viewBox="0 0 20 12"><path d="M2 11 C4 2 12 0 18 1 C16 8 10 12 2 11Z" fill="var(--green)"/></svg>
    <a class="active" style="left:427px">HOME</a>
    <a style="left:508px">ABOUT US</a>
    <a style="left:614px">SERVICES</a>
    <a style="left:714px">TESTIMONIALS</a>
    <a style="left:844px">BLOG</a>
    <a style="left:922px">CONTACT US</a>
  </nav>
  <div class="abs search">
    <svg width="37" height="37" viewBox="0 0 37 37"><circle cx="17" cy="17" r="4.5" fill="none" stroke="#777" stroke-width="1.6"/><line x1="20.5" y1="20.5" x2="24" y2="24" stroke="#777" stroke-width="1.6"/></svg>
  </div>
</header>
<div class="abs brand"><span class="brand-name">Harbor Lane Services</span></div>

<section class="abs hero" role="img" aria-label="City skyline under a blue sky above a wide green park lawn"></section>
<h1 class="abs hero-title">هاربر لين سرفسس ذ.م.م</h1>
<p class="abs hero-sub">Lorem ipsum dolor sit amet, consectetur adipiscing elit tempor incididunt<br>magna aliqua minim veniam, quis nostrud...</p>
<div class="abs btn-solid">LEARN MORE INFO</div>
<div class="abs arrow" style="left:87px"><svg width="12" height="14" viewBox="0 0 12 14"><path d="M8 2 L3 7 L8 12" fill="none" stroke="#fff" stroke-width="2"/></svg></div>
<div class="abs arrow" style="left:1067px"><svg width="12" height="14" viewBox="0 0 12 14"><path d="M4 2 L9 7 L4 12" fill="none" stroke="#fff" stroke-width="2"/></svg></div>

<section>
  <h2 class="abs heading welcome-title">WELCOME TO HARBOR LANE SERVICES W.L.L</h2>
  <p class="abs welcome-text" style="top:738px">Lorem ipsum dolor sit amet, consectetur adipiscing elit, sed do eiusmod tempor incididunt ut labore et dolore magna aliqua. Ut enim ad minim veniam, quis nostrud exercitation ullamco laboris nisi ut aliquip ex ea commodo consequat.occaecat cupidatat non proident...</p>
  <p class="abs welcome-text" style="top:813px">Dolore magna aliqua. Ut enim ad minim veniam, quis nostrud exercitation ullamco laboris nisi ut aliquip ex ea commodo consequat.occaecat cupidatat non proident...</p>
  <div class="abs btn-outline">LEARN MORE INFO</div>
  <div class="abs welcome-photo" role="img" aria-label="Family walking together across a green park"></div>
</section>

<section>
  <div class="abs services-photo" role="img" aria-label="Dimmed interior scene in dark warm tones"></div>
  <div class="abs services-panel"></div>
  <div class="abs services-badge">OUR<br>SERVICES</div>

  <svg class="abs service-leaf" style="top:1058px" width="30" height="22" viewBox="0 0 30 22"><path d="M28 20 C24 4 12 0 2 3 C6 16 16 22 28 20Z" fill="var(--green)"/></svg>
  <div class="abs service-icon" style="top:1064px"><svg width="40" height="40" viewBox="0 0 40 40" fill="none" stroke="#fff" stroke-width="2.4"><line x1="30" y1="6" x2="19" y2="20"/><path d="M15 17 L23 24 L16 34 L6 27Z"/></svg></div>
  <h3 class="abs service-title" style="top:1063px">Tempor Lincididunt</h3>
  <p class="abs service-text" style="top:1084px">Lorem ipsum dolor sit amet, consectetur adipiscing elit, sed do eiusmod tempor incididunt ut labore et dolore magna aliqua.occaecat cupidatat non proident, sunt in culpa qui officia...</p>

  <svg class="abs service-leaf" style="top:1192px" width="30" height="22" viewBox="0 0 30 22"><path d="M28 20 C24 4 12 0 2 3 C6 16 16 22 28 20Z" fill="var(--green)"/></svg>
  <div class="abs service-icon" style="top:1198px"><svg width="40" height="40" viewBox="0 0 40 40" fill="#fff"><rect x="9" y="8" width="22" height="26"/><g fill="var(--green)"><rect x="12" y="11" width="4" height="4"/><rect x="18" y="11" width="4" height="4"/><rect x="24" y="11" width="4" height="4"/><rect x="12" y="18" width="4" height="4"/><rect x="18" y="18" width="4" height="4"/><rect x="24" y="18" width="4" height="4"/><rect x="17" y="26" width="6" height="8"/></g></svg></div>
  <h3 class="abs service-title" style="top:1198px">Tempor Lincididunt</h3>
  <p class="abs service-text" style="top:1219px">Lorem ipsum dolor sit amet, consectetur adipiscing elit, sed do eiusmod tempor incididunt ut labore et dolore magna aliqua.occaecat cupidatat non proident, sunt in culpa qui officia...</p>

  <svg class="abs service-leaf" style="top:1327px" width="30" height="22" viewBox="0 0 30 22"><path d="M28 20 C24 4 12 0 2 3 C6 16 16 22 28 20Z" fill="var(--green)"/></svg>
  <div class="abs service-icon" style="top:1333px"><svg width="40" height="40" viewBox="0 0 40 40" fill="#fff"><path d="M10 18 C10 10 30 10 30 18Z"/><rect x="8" y="19" width="24" height="2"/><rect x="11" y="22" width="3" height="10"/><rect x="18.5" y="22" width="3" height="10"/><rect x="26" y="22" width="3" height="10"/><rect x="7" y="32" width="26" height="3"/></svg></div>
  <h3 class="abs service-title" style="top:1333px">Tempor Lincididunt</h3>
  <p class="abs service-text" style="top:1354px">Lorem ipsum dolor sit amet, consectetur adipiscing elit, sed do eiusmod tempor incididunt ut labore et dolore magna aliqua.occaecat cupidatat non proident, sunt in culpa qui officia...</p>
</section>

<section>
  <h2 class="abs heading blog-title">LATEST BLOG</h2>
  <p class="abs blog-sub">Lorem ipsum dolor sit amet, consectetur adipiscing elit, sed do eiusmod tempor incididunt aliqua.</p>

  <div class="abs post-photo" style="left:132px;background:linear-gradient(135deg,#c9d3da,#6d6f72)" role="img" aria-label="Bright window interior"></div>
  <div class="abs post-photo" style="left:456px;background:linear-gradient(135deg,#e9e7e4,#b9a99a)" role="img" aria-label="Modern kitchen interior"></div>
  <div class="abs post-photo" style="left:779px;background:linear-gradient(135deg,#fbfbfb,#ddd6e6);border:1px solid var(--line)" role="img" aria-label="Light studio backdrop"></div>

  <h3 class="abs post-title" style="left:132px">Pariatur Excepteur Accaecat</h3>
  <h3 class="abs post-title" style="left:456px">Pariatur Excepteur Accaecat</h3>
  <h3 class="abs post-title" style="left:779px">Pariatur Excepteur Accaecat</h3>
  <p class="abs post-text" style="left:132px">At vloreero eos et accusamuos et accusamuss ettodilo rsocimuupiditate non provident...</p>
  <p class="abs post-text" style="left:456px">At vloreero eos et accusamuos et accusamuss ettodilo rsocimuupiditate non provident...</p>
  <p class="abs post-text" style="left:779px">At vloreero eos et accusamuos et accusamuss ettodilo rsocimuupiditate non provident...</p>
  <div class="abs post-meta" style="left:132px"><svg width="10" height="10" viewBox="0 0 10 10"><rect x="0.5" y="1.5" width="9" height="8" fill="none" stroke="var(--green)"/><rect x="0.5" y="1.5" width="9" height="2.5" fill="var(--green)"/></svg>20 MAY 2017<span class="sep">|</span><svg width="12" height="10" viewBox="0 0 12 10"><path d="M1 4.5 C1 1 11 1 11 4.5 C11 7.5 5 8 3 7.5 L1 9.5 L1.8 6.5 C1.2 6 1 5.2 1 4.5Z" fill="none" stroke="var(--green)"/></svg>Comments (05)</div>
  <div class="abs post-meta" style="left:456px"><svg width="10" height="10" viewBox="0 0 10 10"><rect x="0.5" y="1.5" width="9" height="8" fill="none" stroke="var(--green)"/><rect x="0.5" y="1.5" width="9" height="2.5" fill="var(--green)"/></svg>20 MAY 2017<span class="sep">|</span><svg width="12" height="10" viewBox="0 0 12 10"><path d="M1 4.5 C1 1 11 1 11 4.5 C11 7.5 5 8 3 7.5 L1 9.5 L1.8 6.5 C1.2 6 1 5.2 1 4.5Z" fill="none" stroke="var(--green)"/></svg>Comments (05)</div>
  <div class="abs post-meta" style="left:779px"><svg width="10" height="10" viewBox="0 0 10 10"><rect x="0.5" y="1.5" width="9" height="8" fill="none" stroke="var(--green)"/><rect x="0.5" y="1.5" width="9" height="2.5" fill="var(--green)"/></svg>20 MAY 2017<span class="sep">|</span><svg width="12" height="10" viewBox="0 0 12 10"><path d="M1 4.5 C1 1 11 1 11 4.5 C11 7.5 5 8 3 7.5 L1 9.5 L1.8 6.5 C1.2 6 1 5.2 1 4.5Z" fill="none" stroke="var(--green)"/></svg>Comments (05)</div>
</section>

<section>
  <div class="abs testimonial"></div>
  <div class="abs avatar" role="img" aria-label="Client portrait"></div>
  <div class="abs divider"></div>
  <p class="abs quote">“Lorem ipsum dolor sit amet, consectetur adipiscing elit, sed do eiusmod tempor incididunt ut labore et dolore magna aliqua. Ut enim ad minim veniam, quis nostrud exercitation ullamco laboris nisi ut aliquip ex ea commodo....</p>
  <p class="abs quote-name">- MIRA HADDAD &nbsp;<span style="letter-spacing:1px">★★★★☆</span></p>
</section>

<footer>
  <div class="abs footer"></div>
  <div class="abs footer-brand"><span class="brand-name">Harbor Lane Services</span></div>

  <h4 class="abs foot-head" style="left:363px">QUICK LINKS</h4>
  <ul class="abs foot-links">
    <li>Home</li><li>About Us</li><li>Services</li><li>Testimonials</li><li>Blog</li><li>Contact us</li>
  </ul>

  <h4 class="abs foot-head" style="left:546px">NEWSLETTER</h4>
  <p class="abs news-text">Enter your email address to receive the latest news and notes from our blog.</p>
  <div class="abs news-input">Enter Your Mail Id</div>
  <div class="abs news-btn">SUBSCRIBE</div>

  <h4 class="abs foot-head" style="left:905px">CONTACT INFO</h4>
  <div class="abs contact-row" style="top:2186px"><svg width="11" height="11" viewBox="0 0 11 11"><path d="M1 3 C1 1 3 1 5.5 1 C8 1 10 1 10 3 L8 4 L7 3 L4 3 L3 4Z M2 5 H9 V10 H2Z" fill="#555"/></svg>(555) 014-2290</div>
  <div class="abs contact-row" style="top:2214px"><svg width="11" height="11" viewBox="0 0 11 11"><rect x="2.5" y="0.5" width="6" height="3" fill="none" stroke="#555"/><rect x="0.5" y="3.5" width="10" height="5" fill="#555"/><rect x="2.5" y="7" width="6" height="3.5" fill="#fff" stroke="#555"/></svg>(555) 014-2290</div>
  <div class="abs contact-row" style="top:2243px"><svg width="11" height="11" viewBox="0 0 11 11"><rect x="0.5" y="2" width="10" height="7" fill="none" stroke="#555"/><path d="M0.5 2 L5.5 6 L10.5 2" fill="none" stroke="#555"/></svg><span style="text-decoration:underline">hello@harborlane.example</span></div>
  <div class="abs contact-row" style="top:2270px"><svg width="11" height="13" viewBox="0 0 11 13"><path d="M5.5 12.5 C2 8 1 6 1 4.5 A4.5 4.5 0 0 1 10 4.5 C10 6 9 8 5.5 12.5Z" fill="#555"/><circle cx="5.5" cy="4.5" r="1.6" fill="#fff"/></svg>#2868 Lorem ipsum dolor sit amet, consectetur</div>

  <div class="abs foot-rule"></div>
  <p class="abs copyright">©2017 harbor lane services W.L.L | all rights reserved</p>
  <p class="abs follow">Follow Us :</p>
  <div class="abs social" style="left:888px"></div>
  <div class="abs social" style="left:921px"></div>
  <div class="abs social" style="left:955px"></div>
  <div class="abs social" style="left:988px"></div>
  <div class="abs social" style="left:1021px"></div>
</footer>

</body>
</html>
```